Verdant Mist Irrigation LLC Business Card

Ok, first off let me thank you for taking the time to participate in this project !! I have my business logo that I want incorporated into business card design . My irrigation business is located in a very upscale part of town and we do high end homes . So with that said I'm planning on these cards being plastic credit card type cards. I would like them to be two sided . I'm thinking something bold , yet classy and clean . Not too busy . We do different types of work . 80% irrigation service and installation . 15% landscape lighting and the other 5% drainage and hardscapes ! I have a website that I want listed on it as well as our address , phone number and of course my name and title .
Updates

Target Market(s)

Upscale homeowners and architects

Industry/Entity Type

Landscape

Requirements
Must have
• Company logo, website, address , phone number , name , title , services offered

Www.VerdantMistIrrigation-demo.com
Marcus Hollen owner
205-555-0148
Verdant Mist Irrigation LLC
P.O. Box 947215
Birmingham, Alabama 35290

```html
<!DOCTYPE html>
<html lang="en">
<head>
<meta charset="utf-8">
<title>Verdant Mist Irrigation LLC – Business Card</title>
<link rel="stylesheet" href="https://fonts.googleapis.com/css2?family=Open+Sans:ital,wght@0,700;1,400;1,600;1,700&display=swap">
<style>
  :root {
    --page-bg: #ecebe8;
    --card-bg: #ffffff;
    --ink: #1a1a1a;
    --brand-green: #6cae3e;
    --brand-blue: #1a9ad6;
    --panel-light: #e6f4fc;
    --panel-deep: #0f9be0;
    --shadow: rgba(0, 0, 0, 0.22);
  }
  * { margin: 0; padding: 0; box-sizing: border-box; }
  html, body { width: 1200px; height: 999px; overflow: hidden; }
  body {
    background: var(--page-bg);
    font-family: "Open Sans", Arial, sans-serif;
    color: var(--ink);
    position: relative;
  }
  .card {
    position: absolute;
    left: 250px;
    width: 700px;
    height: 400px;
    background: var(--card-bg);
    box-shadow: 0 6px 18px var(--shadow);
    overflow: hidden;
  }
  .card--front { top: 50px; }
  .card--back { top: 520px; }

  /* Brand lockup */
  .brand {
    position: absolute;
    display: flex;
    flex-direction: column;
    align-items: center;
  }
  .brand__dot {
    border-radius: 50%;
    background: var(--brand-blue);
  }
  .brand__name {
    font-weight: 700;
    font-style: normal;
    color: var(--brand-green);
    white-space: nowrap;
  }
  .card--front .brand { left: 0; right: 0; top: 70px; }
  .card--front .brand__dot { width: 120px; height: 120px; margin-bottom: 22px; }
  .card--front .brand__name { font-size: 42px; }
  .front__web {
    position: absolute;
    left: 0; right: 0; top: 292px;
    text-align: center;
    font-style: italic;
    font-size: 25px;
    color: var(--brand-blue);
  }

  /* Back */
  .back__panel { position: absolute; inset: 0; }
  .card--back .brand { left: 62px; width: 300px; top: 56px; }
  .card--back .brand__dot { width: 92px; height: 92px; margin-bottom: 12px; }
  .card--back .brand__name { font-size: 25px; }

  .services {
    position: absolute;
    left: 42px;
    top: 252px;
    font-style: italic;
    font-weight: 600;
    font-size: 19px;
    line-height: 27px;
  }
  .services__title { color: var(--brand-blue); font-weight: 700; }
  .services__list { list-style: none; }
  .services__list li::before {
    content: "\2022";
    color: var(--brand-blue);
    margin-right: 5px;
  }

  .contact {
    position: absolute;
    right: 30px;
    text-align: right;
    font-style: italic;
  }
  .contact__name { top: 44px; font-weight: 700; font-size: 23px; line-height: 28px; }
  .contact__title { top: 72px; font-size: 18px; }
  .contact__address { top: 210px; font-weight: 600; font-size: 17px; line-height: 24px; }
  .contact__phone, .contact__web {
    display: flex; align-items: center; gap: 6px; font-weight: 700;
  }
  .contact__phone { top: 303px; font-size: 23px; }
  .contact__web { top: 337px; font-size: 16px; }
  .icon { width: 20px; height: 20px; flex: none; }
</style>
</head>
<body>

  <section class="card card--front" aria-label="Card front">
    <div class="brand">
      <div class="brand__dot"></div>
      <div class="brand__name">Verdant Mist Irrigation</div>
    </div>
    <p class="front__web">www.verdantmistirrigation-demo.com</p>
  </section>

  <section class="card card--back" aria-label="Card back">
    <svg class="back__panel" viewBox="0 0 700 400" width="700" height="400" aria-hidden="true">
      <defs>
        <linearGradient id="panelFade" x1="0" y1="0" x2="0" y2="1">
          <stop offset="0" stop-color="var(--panel-light)"/>
          <stop offset="0.55" stop-color="#8fd2f4"/>
          <stop offset="1" stop-color="var(--panel-deep)"/>
        </linearGradient>
      </defs>
      <polygon points="481,0 700,0 700,400 340,400" fill="url(#panelFade)"/>
    </svg>

    <div class="brand">
      <div class="brand__dot"></div>
      <div class="brand__name">Verdant Mist Irrigation</div>
    </div>

    <div class="services">
      <p class="services__title">Services Offered:</p>
      <ul class="services__list">
        <li>Irrigation Service &amp; Installation</li>
        <li>Landscape Lighting</li>
        <li>Drainage &amp; Hardscapes</li>
      </ul>
    </div>

    <p class="contact contact__name">Marcus Hollen</p>
    <p class="contact contact__title">Owner</p>
    <p class="contact contact__address">P.O. Box 947215<br>Birmingham, Alabama 35290</p>
    <p class="contact contact__phone">205-555-0148
      <svg class="icon" viewBox="0 0 20 20" aria-hidden="true">
        <path d="M3 8c0-3 3-4 7-4s7 1 7 4l-3 1-1-2H7L6 9z" fill="#fff"/>
        <rect x="6" y="10" width="8" height="5" rx="1" fill="#fff"/>
      </svg>
    </p>
    <p class="contact contact__web">www.verdantmistirrigation-demo.com
      <svg class="icon" viewBox="0 0 20 20" aria-hidden="true">
        <circle cx="10" cy="10" r="8" fill="none" stroke="#fff" stroke-width="1.6"/>
        <ellipse cx="10" cy="10" rx="3.5" ry="8" fill="none" stroke="#fff" stroke-width="1.4"/>
        <line x1="2" y1="10" x2="18" y2="10" stroke="#fff" stroke-width="1.4"/>
      </svg>
    </p>
  </section>

</body>
</html>
```